Power Point Showing our WHY: R4V

Project Description:
This PowerPoint design project aims to humanize critical educational statistics by transforming data into a powerful visual narrative. The goal is to put a face to the data, making abstract percentages more tangible and emotionally resonant for audiences.

The presentation begins with a single, impactful visual: 100 K–12 students, diverse in race and ethnicity, representing the full spectrum of learners across America.

Slide Progression & Visual Design:
Slide 1: "The Starting Line – 100 Students"
A visual display of 100 illustrated or photographic K–12 students.
Representation includes diversity in race, ethnicity, gender, and clothing to reflect real classrooms.
This slide sets the stage: every student matters.
Slide 2: "The First Drop – High School Graduation"
20 students fade away, showing the stark reality that only 80% graduate from high school.
Remaining 80 students stay on screen, reinforcing the message: not all students make it to the finish line.
Slide 3: "College Completion – A Narrowing Path"
From the 80 remaining students, another 35 fade away, illustrating that only 56% of students earn a college degree.
This leaves 45 students visible, showing the significant drop-off even after high school graduation.
Slide 4: "Low-Income Learners – The Equity Gap"
The image resets to the original 100 students.
This time, 87 students fade away, leaving only 13 standing, representing the 13% of low-income students who earn a college degree.
The emotional impact is amplified by the dramatic reduction in students who overcome economic barriers.
Design Notes:
Use consistent character illustrations or silhouettes for cohesion.
Employ subtle animations for "fading out" to enhance storytelling.
Slides should have minimal text—statistics should be overlaid in bold, clean typography.
Backgrounds should remain neutral or slightly muted to keep the focus on the students.
I am including out template to use

```html
<!DOCTYPE html>
<html lang="en">
<head>
<meta charset="utf-8">
<title>R4V – Showing Our Why</title>
<link href="https://fonts.googleapis.com/css2?family=Quicksand:wght@500;600;700&display=swap" rel="stylesheet">
<style>
  :root {
    --stage: #878787;
    --slide-bg: #ffffff;
    --header: #1d434e;
    --footer: #b10d57;
    --accent-orange: #ff5a0a;
    --accent-teal: #14a89a;
    --white: #ffffff;
    --crowd-deep: #6b4a3a;
    --crowd-mid: #3d6a8a;
    --crowd-warm: #c9a24a;
    --crowd-faded: #e6e8ea;
  }
  * { box-sizing: border-box; margin: 0; padding: 0; }
  html, body { width: 1200px; height: 744px; overflow: hidden; }
  body {
    background: var(--stage);
    font-family: "Quicksand", sans-serif;
    position: relative;
  }
  .slide {
    position: absolute;
    width: 537px;
    height: 302px;
    background: var(--slide-bg);
    box-shadow: 0 6px 18px rgba(0,0,0,.28);
    overflow: hidden;
  }
  .slide--start { left: 42px; top: 48px; }
  .slide--highschool { left: 621px; top: 48px; }
  .slide--college { left: 42px; top: 395px; }
  .slide--equity { left: 621px; top: 395px; }

  .slide__header {
    height: 36px;
    background: var(--header);
    color: var(--white);
    font-weight: 600;
    font-size: 19px;
    display: flex;
    align-items: center;
    justify-content: center;
    letter-spacing: .2px;
  }
  .slide__crowd {
    position: absolute;
    left: 34px;
    top: 52px;
    width: 468px;
    height: 186px;
    border-radius: 50% / 42%;
  }
  .crowd--full {
    background: radial-gradient(ellipse at center, #ffffff 0 30%, transparent 31%),
                linear-gradient(90deg, var(--crowd-deep), var(--crowd-mid) 35%, var(--crowd-warm) 65%, var(--crowd-mid));
  }
  .crowd--eighty {
    background: radial-gradient(ellipse at center, #ffffff 0 30%, transparent 31%),
                linear-gradient(180deg, var(--crowd-faded) 0 18%, transparent 18%),
                linear-gradient(90deg, var(--crowd-deep), var(--crowd-mid) 35%, var(--crowd-warm) 65%, var(--crowd-mid));
  }
  .crowd--fortyfive {
    background: radial-gradient(ellipse at center, #ffffff 0 30%, transparent 31%),
                linear-gradient(180deg, var(--crowd-faded) 0 42%, transparent 42%),
                linear-gradient(90deg, var(--crowd-deep), var(--crowd-mid) 40%, var(--crowd-faded) 66%, var(--crowd-faded));
  }
  .crowd--thirteen {
    background: radial-gradient(ellipse at center, #ffffff 0 30%, transparent 31%),
                linear-gradient(180deg, var(--crowd-faded) 0 42%, transparent 42%),
                linear-gradient(90deg, var(--crowd-faded) 0 10%, var(--crowd-deep) 12%, var(--crowd-mid) 40%, var(--crowd-faded) 56%, var(--crowd-faded));
  }
  .slide__caption {
    position: absolute;
    left: 0; right: 0;
    top: 244px;
    text-align: center;
    font-weight: 600;
    font-size: 19px;
    line-height: 24px;
    color: var(--accent-orange);
    white-space: nowrap;
  }
  .slide__caption--lead { font-size: 24px; line-height: 28px; top: 240px; }
  .slide__caption .teal { color: var(--accent-teal); }

  .slide__footer {
    position: absolute;
    left: 0; right: 0; bottom: 0;
    height: 19px;
    background: var(--footer);
    display: flex;
    align-items: center;
    padding-left: 33px;
  }
  .brand-name {
    color: var(--white);
    font-weight: 600;
    font-size: 7px;
    letter-spacing: .2px;
  }
</style>
</head>
<body>

  <section class="slide slide--start">
    <header class="slide__header">The Starting Line – 100 Students</header>
    <div class="slide__crowd crowd--full" role="img" aria-label="Illustrated crowd of 100 diverse students standing in an oval"></div>
    <p class="slide__caption slide__caption--lead">Every <span class="teal">Student</span> Matters</p>
    <footer class="slide__footer"><span class="brand-name">R4V LEARNING ALLIANCE</span></footer>
  </section>

  <section class="slide slide--highschool">
    <header class="slide__header">The First Drop – High School Graduation</header>
    <div class="slide__crowd crowd--eighty" role="img" aria-label="Illustrated crowd of students with 20 faded away, 80 remaining"></div>
    <p class="slide__caption">Not all students <span class="teal">make it to the</span> finish line</p>
    <footer class="slide__footer"><span class="brand-name">R4V LEARNING ALLIANCE</span></footer>
  </section>

  <section class="slide slide--college">
    <header class="slide__header">College Completion – A Narrowing Path</header>
    <div class="slide__crowd crowd--fortyfive" role="img" aria-label="Illustrated crowd of students with most faded away, a front group remaining"></div>
    <p class="slide__caption">Only 56% of <span class="teal">students earn a</span> college degree</p>
    <footer class="slide__footer"><span class="brand-name">R4V LEARNING ALLIANCE</span></footer>
  </section>

  <section class="slide slide--equity">
    <header class="slide__header">Low-Income Learners – The Equity Gap</header>
    <div class="slide__crowd crowd--thirteen" role="img" aria-label="Illustrated crowd of students with 87 faded away, 13 remaining"></div>
    <p class="slide__caption">Not all students <span class="teal">make it to the</span> finish line</p>
    <footer class="slide__footer"><span class="brand-name">R4V LEARNING ALLIANCE</span></footer>
  </section>

</body>
</html>
```